Willow Creek Gatherings Event Planning in need of a design!!

Event Planning company, does a variety of events. I like simple more rustic designs focused on almond blossoms. We are based out of Northern California, the heart of almond country. I would like to see colors in light pinks, beige, light browns, whites or creams. the final design should communicate rustic simplicity. Below are some pictures of Almond blossoms and design ideas I prefer the one called Tulip Grove. Thanks

Target Market(s)

Women in the mid twenties and older. They should be in the upper middle class in need of an amazing party design and coordinator

Industry/Entity Type

Event Planning

Contact Information for Business Card

Maren Lockwood 530-624-0295almondbaffairs@gmail.comalmondblossomaffairs.com

Font styles to use
Other font styles liked:
• Amatic SC

Requirements
Must have
• almond blossom
• my information
• simplicity
Nice to have
• rustic design
• vintage feel
• whimsical
Should not have
• i like pink but not over the top

```html
<!DOCTYPE html>
<html lang="en">
<head>
<meta charset="utf-8">
<title>Willow Creek Gatherings — Business Cards</title>
<link href="https://fonts.googleapis.com/css2?family=Questrial&family=Open+Sans:wght@400;600&display=swap" rel="stylesheet">
<style>
  :root {
    --page-bg: #efebe6;
    --card-white: #ffffff;
    --brand-brown: #9a7656;
    --band-brown: #9c7656;
    --rule-grey: #a7a8ab;
    --text-light: #ffffff;
    --orchard-sky: #dfe9f1;
    --orchard-blossom: #efeae6;
    --orchard-green: #6f9a4a;
    --orchard-ground: #cfc6bb;
  }
  * { box-sizing: border-box; margin: 0; padding: 0; }
  html, body {
    width: 1200px; height: 900px; overflow: hidden;
    background: var(--page-bg);
  }
  .canvas { position: relative; width: 1200px; height: 900px; }

  .card {
    position: absolute;
    width: 560px; height: 320px;
    overflow: hidden;
    box-shadow: 0 10px 28px rgba(60, 45, 30, 0.18);
  }

  /* Front */
  .card-front { left: 70px; top: 120px; }
  .orchard-photo {
    position: absolute; inset: 0;
    background:
      linear-gradient(180deg, transparent 62%, var(--orchard-ground) 80%, #bdb3a7 100%),
      linear-gradient(90deg, var(--orchard-green) 0%, #9fb98a 22%, var(--orchard-blossom) 42%, #e4ddd6 70%, #b9c9a4 100%),
      linear-gradient(180deg, var(--orchard-sky) 0%, var(--orchard-blossom) 45%);
    background-blend-mode: normal, multiply, normal;
  }
  .front-name-box {
    position: absolute; left: 60px; top: 178px;
    width: 340px; height: 98px;
    background: rgba(255, 255, 255, 0.94);
    display: flex; align-items: center; justify-content: center;
  }
  .brand-name {
    font-family: "Questrial", sans-serif;
    font-weight: 400;
    color: var(--brand-brown);
    letter-spacing: 1px;
    text-align: center;
    line-height: 1.1;
  }
  .front-name-box .brand-name { font-size: 27px; }

  /* Back */
  .card-back { left: 570px; top: 440px; background: var(--card-white); }
  .back-top {
    position: absolute; left: 0; top: 0; width: 100%; height: 168px;
    background: linear-gradient(180deg, #f4f4f4 0%, var(--card-white) 60%);
    display: flex; align-items: center; justify-content: center;
  }
  .back-top .brand-name { font-size: 34px; }
  .back-rule {
    position: absolute; left: 0; top: 168px; width: 100%; height: 6px;
    background: var(--rule-grey);
  }
  .back-band {
    position: absolute; left: 0; top: 180px; width: 100%; bottom: 0;
    background: var(--band-brown);
    color: var(--text-light);
    font-family: "Open Sans", sans-serif;
  }
  .contact-list {
    position: absolute; right: 230px; top: 26px;
    list-style: none; text-align: right;
    font-size: 15px; line-height: 28px;
  }
  .contact-list li { display: flex; align-items: center; justify-content: flex-end; gap: 8px; }
  .contact-list svg { width: 13px; height: 13px; fill: var(--text-light); flex: none; }
  .person-name {
    position: absolute; left: 380px; top: 22px;
    font-size: 18px; font-weight: 600;
  }
</style>
</head>
<body>
<main class="canvas">

  <section class="card card-front" aria-label="Business card front">
    <div class="orchard-photo" role="img" aria-label="Photograph of an almond orchard in bloom, rows of blossoming trees over green grass"></div>
    <div class="front-name-box">
      <p class="brand-name">Willow Creek Gatherings</p>
    </div>
  </section>

  <section class="card card-back" aria-label="Business card back">
    <div class="back-top">
      <p class="brand-name">Willow Creek Gatherings</p>
    </div>
    <div class="back-rule"></div>
    <div class="back-band">
      <ul class="contact-list">
        <li>530-817-4362
          <svg viewBox="0 0 24 24" aria-hidden="true"><path d="M6.6 10.8a15.1 15.1 0 0 0 6.6 6.6l2.2-2.2c.3-.3.7-.4 1-.2 1.1.4 2.3.6 3.6.6.6 0 1 .4 1 1V20c0 .6-.4 1-1 1A17 17 0 0 1 3 4c0-.6.4-1 1-1h3.5c.6 0 1 .4 1 1 0 1.3.2 2.5.6 3.6.1.3 0 .7-.2 1z"/></svg>
        </li>
        <li>willowcgather@mailbox.test
          <svg viewBox="0 0 24 24" aria-hidden="true"><path d="M2 5h20v14H2z M3.5 6.5 12 13l8.5-6.5" stroke="#9c7656" stroke-width="1.5"/></svg>
        </li>
        <li>willowcreekgatherings.test
          <svg viewBox="0 0 24 24" aria-hidden="true"><circle cx="12" cy="12" r="10"/><path d="M2 12h20M12 2c3 3 3 17 0 20M12 2c-3 3-3 17 0 20" stroke="#9c7656" stroke-width="1.4" fill="none"/></svg>
        </li>
      </ul>
      <p class="person-name">Maren Lockwood</p>
    </div>
  </section>

</main>
</body>
</html>
```